Business Card Design for Varomir Facility Services

We are looking for a Business Card Design for the Company "Varomir Facility Services."
Front side:
- Company Logo (small)
- Company Name, address, pohone, website and personal data.
- white background, for text e.g. company colors (blue or green like in the logo)
Please use following data:
Company data:
Varomir Facility Services Kostelac
Birkenhaldweg 14
6341 Talwiesen
www.varomir-fs.ch
Person data:
Tarik Kostelac
Geschäftsführer
+41 76 519 47 83
info@varomir-fs.ch
Back side:
could be colored in blue or green
please use a big logo sing and some smaller icons to say what is all beeing offered in facility services, like cleaning, maintenance cleaning
industrial cleaning, caretaking, gardening, disposal. There is no need for everyone of the icons if there are similar or an icon is standing for more of them.
colors to use:
blue: HEX 246BB0
green: HEX 52B33E

```html
<!DOCTYPE html>
<html lang="de">
<head>
<meta charset="utf-8">
<title>Varomir Facility Services – Visitenkarte</title>
<link rel="stylesheet" href="https://fonts.googleapis.com/css2?family=Roboto:wght@400;500;700;900&display=swap">
<style>
  :root {
    --brand-blue: #246bb0;
    --panel-blue: #02509a;
    --brand-green: #52b33e;
    --contact-green: #2fb33a;
    --white: #ffffff;
    --ink: #111111;
    --stage: #e9eaec;
  }
  * { box-sizing: border-box; margin: 0; padding: 0; }
  html, body { width: 1200px; height: 1200px; overflow: hidden; }
  body {
    background: var(--stage);
    font-family: "Roboto", Arial, sans-serif;
    display: flex;
    flex-direction: column;
    align-items: center;
    justify-content: center;
    gap: 40px;
  }
  .card {
    position: relative;
    width: 840px;
    height: 500px;
    border-radius: 34px;
    overflow: hidden;
    box-shadow: 0 6px 18px rgba(0,0,0,.18);
  }

  /* Back side */
  .card-back { background: var(--brand-blue); color: var(--white); }
  .back-brand {
    position: absolute; top: 70px; left: 0; right: 0;
    text-align: center; font-weight: 700;
  }
  .back-brand .brand-mark {
    width: 54px; height: 54px; border-radius: 50%;
    background: var(--white); margin: 0 auto 18px;
  }
  .back-brand .brand-name { font-size: 88px; letter-spacing: 6px; line-height: 1; text-transform: uppercase; }
  .back-brand .brand-sub { font-size: 30px; letter-spacing: 9px; margin-top: 8px; text-transform: uppercase; }
  .services {
    position: absolute; left: 0; right: 0; bottom: 46px;
    display: flex; justify-content: center; gap: 46px;
    list-style: none;
  }
  .service { width: 120px; text-align: center; }
  .service-icon {
    width: 92px; height: 92px; margin: 0 auto 10px;
    border-radius: 50%; background: var(--white);
    border: 3px solid var(--white);
    box-shadow: inset 0 0 0 3px var(--brand-blue);
    display: flex; align-items: center; justify-content: center;
  }
  .service-label { font-size: 13px; font-weight: 700; line-height: 1.1; text-transform: uppercase; }

  /* Front side */
  .card-front { background: var(--white); }
  .front-shape { position: absolute; inset: 0; }
  .front-brand {
    position: absolute; left: 60px; top: 150px;
    color: var(--brand-blue); font-weight: 700;
    display: flex; align-items: center; gap: 16px;
  }
  .front-brand .brand-mark { width: 40px; height: 40px; border-radius: 50%; background: var(--brand-green); flex: none; }
  .front-brand .brand-name { font-size: 64px; line-height: 1; letter-spacing: 3px; text-transform: uppercase; }
  .front-brand .brand-sub { font-size: 22px; letter-spacing: 6px; margin-top: 8px; text-transform: uppercase; }
  .contact {
    position: absolute; left: 478px; top: 170px; color: var(--white);
  }
  .contact-name { font-size: 30px; font-weight: 700; }
  .contact-role { font-size: 17px; margin-top: 2px; }
  .contact-company { font-size: 17px; font-weight: 700; color: var(--contact-green); margin-top: 20px; }
  .contact-address { font-size: 18px; line-height: 1.3; margin-top: 2px; }
  .contact-lines { list-style: none; margin-top: 10px; font-size: 18px; line-height: 1.45; }
  .contact-lines li { display: flex; align-items: center; gap: 10px; }
  .contact-lines svg { width: 16px; height: 16px; flex: none; }
  .contact-lines b { font-weight: 700; }
</style>
</head>
<body>

<section class="card card-back" aria-label="Rückseite">
  <div class="back-brand">
    <div class="brand-mark"></div>
    <div class="brand-name">Varomir</div>
    <div class="brand-sub">Facility Services</div>
  </div>
  <ul class="services">
    <li class="service">
      <div class="service-icon">
        <svg width="44" height="44" viewBox="0 0 44 44" fill="var(--brand-blue)"><rect x="20" y="3" width="4" height="16" rx="2"/><rect x="10" y="18" width="24" height="7" rx="2"/><path d="M11 25h22l-2 14H13z"/></svg>
      </div>
      <div class="service-label">Maintenance<br>Cleaning</div>
    </li>
    <li class="service">
      <div class="service-icon">
        <svg width="46" height="46" viewBox="0 0 46 46" fill="none" stroke="var(--brand-blue)" stroke-width="3" stroke-linejoin="round"><path d="M23 40 C8 29 4 22 4 15 a9 9 0 0 1 19 -3 a9 9 0 0 1 19 3 c0 7 -4 14 -19 25z"/></svg>
      </div>
      <div class="service-label">Caretaking</div>
    </li>
    <li class="service">
      <div class="service-icon">
        <svg width="44" height="44" viewBox="0 0 44 44" fill="var(--brand-blue)"><circle cx="22" cy="11" r="7"/><circle cx="22" cy="11" r="3" fill="#fff"/><rect x="21" y="17" width="2" height="9"/><path d="M10 26h24l-3 14H13z"/></svg>
      </div>
      <div class="service-label">Gardening</div>
    </li>
    <li class="service">
      <div class="service-icon">
        <svg width="44" height="44" viewBox="0 0 44 44" fill="var(--brand-blue)"><rect x="8" y="8" width="28" height="4" rx="1"/><rect x="18" y="4" width="8" height="4" rx="1"/><path d="M11 14h22l-2 26H13z"/><g fill="#fff"><rect x="16" y="18" width="2" height="18"/><rect x="21" y="18" width="2" height="18"/><rect x="26" y="18" width="2" height="18"/></g></svg>
      </div>
      <div class="service-label">Disposal</div>
    </li>
  </ul>
</section>

<section class="card card-front" aria-label="Vorderseite">
  <svg class="front-shape" width="840" height="500" viewBox="0 0 840 500" aria-hidden="true">
    <polygon points="560,0 840,0 840,500 452,500 452,148" fill="var(--panel-blue)"/>
    <polyline points="545,0 440,138 440,500" fill="none" stroke="var(--ink)" stroke-width="4"/>
  </svg>
  <div class="front-brand">
    <div class="brand-mark"></div>
    <div>
      <div class="brand-name">Varomir</div>
      <div class="brand-sub">Facility Services</div>
    </div>
  </div>
  <div class="contact">
    <div class="contact-name">Tarik Kostelac</div>
    <div class="contact-role">Geschäftsführer</div>
    <div class="contact-company">Varomir Facility Services Kostelac</div>
    <div class="contact-address">Birkenhaldweg 14<br>6341 Talwiesen</div>
    <ul class="contact-lines">
      <li><svg viewBox="0 0 16 16" fill="#fff"><path d="M3 1l3 3-2 2c1 2 3 4 5 5l2-2 3 3-2 3C7 14 2 9 1 3z"/></svg>+41 76 519 47 83</li>
      <li><svg viewBox="0 0 16 16" fill="none" stroke="#fff" stroke-width="1.6"><rect x="1" y="3" width="14" height="10"/><path d="M1 3l7 6 7-6"/></svg>info@varomir-fs.ch</li>
      <li><svg viewBox="0 0 16 16" fill="none" stroke="#fff" stroke-width="1.3"><circle cx="8" cy="8" r="6.5"/><ellipse cx="8" cy="8" rx="3" ry="6.5"/><path d="M1.5 8h13"/></svg><span>www.<b>varomir-fs</b>.ch</span></li>
    </ul>
  </div>
</section>

</body>
</html>
```